Indy Film Production Company/Studio

We need a business card designed from an existing logo. We are a digital studio/production company that caters to creating genre entertainment, like Action, Horror, and martial arts. The card along with the logo will be used to Brand the company from letter heads to banners. The design will also be used for postcards and Brochures. It should be professional and masculine.
Updates

Thank you to all the designers who have participated. I'm narrowing down who it will be. Thank you again.

Target Market(s)

Investors, Networks, Producers, and actors

Industry/Entity Type

Film Production

Contact Information for Business Card

Teodoro Valbuena
Producer/Writer/Director
www.kestrelpicturehouse.example

Requirements
Must have
• Website address, Facebook icon and Twitter icon possibly in the back of the card.
Nice to have
• Logline of Company: Follow The Action.

```html
<!DOCTYPE html>
<html lang="en">
<head>
<meta charset="utf-8">
<title>Kestrel Picture House — Business Card</title>
<link href="https://fonts.googleapis.com/css2?family=Montserrat:ital,wght@1,800&family=Roboto:wght@400;700&display=swap" rel="stylesheet">
<style>
  :root {
    --backdrop: #a9a7a7;
    --card-dark: #2b2927;
    --card-light: #f1f1f1;
    --brand-red: #d2312a;
    --ink: #1c1c1c;
    --divider: #dcdcdc;
  }
  html, body {
    margin: 0;
    padding: 0;
    width: 1200px;
    height: 1200px;
    overflow: hidden;
    background: var(--backdrop);
  }
  .canvas {
    position: relative;
    width: 1200px;
    height: 1200px;
    font-family: "Roboto", Arial, sans-serif;
  }
  .card {
    position: absolute;
    width: 713px;
    height: 418px;
  }
  .card--front {
    left: 238px;
    top: 118px;
    background: var(--card-dark);
    display: flex;
    align-items: center;
    justify-content: center;
  }
  .card--back {
    left: 230px;
    top: 644px;
    background: var(--card-light);
  }
  .brand-name {
    margin: 0;
    color: var(--brand-red);
    font-family: "Roboto", Arial, sans-serif;
    font-weight: 700;
    text-transform: uppercase;
    text-align: center;
    line-height: 1.05;
    letter-spacing: 1px;
  }
  .card--front .brand-name {
    font-size: 44px;
    transform: translateY(-8px);
  }
  .card--back .brand-name {
    position: absolute;
    left: 40px;
    width: 270px;
    top: 160px;
    font-size: 32px;
  }
  .divider {
    position: absolute;
    left: 338px;
    top: 74px;
    width: 1px;
    height: 272px;
    background: var(--divider);
  }
  .contact {
    position: absolute;
    left: 375px;
    top: 110px;
    width: 320px;
    color: var(--ink);
  }
  .contact__name {
    margin: 0;
    font-family: "Montserrat", Arial, sans-serif;
    font-style: italic;
    font-weight: 800;
    font-size: 26px;
    letter-spacing: 0.3px;
    white-space: nowrap;
  }
  .contact__role {
    margin: 6px 0 0;
    color: var(--brand-red);
    font-size: 16px;
  }
  .contact__list {
    list-style: none;
    margin: 30px 0 0;
    padding: 0;
    font-size: 17px;
    line-height: 28px;
  }
  .contact__item {
    display: flex;
    align-items: center;
    gap: 14px;
    white-space: nowrap;
  }
  .contact__icon {
    width: 18px;
    height: 14px;
    fill: var(--brand-red);
    flex: none;
  }
  .social {
    display: flex;
    align-items: center;
    gap: 8px;
    margin-top: 8px;
    font-size: 17px;
  }
  .social__dot {
    width: 20px;
    height: 20px;
    border-radius: 50%;
    background: var(--brand-red);
    flex: none;
  }
  .social__handle {
    margin-left: 6px;
  }
</style>
</head>
<body>
<main class="canvas">
  <section class="card card--front" aria-label="Card front">
    <h1 class="brand-name">Kestrel<br>Picture House</h1>
  </section>

  <section class="card card--back" aria-label="Card back">
    <h2 class="brand-name">Kestrel<br>Picture House</h2>
    <div class="divider"></div>
    <div class="contact">
      <p class="contact__name">Teodoro Valbuena</p>
      <p class="contact__role">Producer/Writer/Director</p>
      <ul class="contact__list">
        <li class="contact__item">
          <svg class="contact__icon" viewBox="0 0 18 14" aria-hidden="true">
            <path d="M1 3 Q9 -1 17 3 L17 5 L13 5 L12 3 L6 3 L5 5 L1 5 Z"/>
            <path d="M4 6 L14 6 L16 13 L2 13 Z"/>
          </svg>
          <span>+00 111 222 3333</span>
        </li>
        <li class="contact__item">
          <svg class="contact__icon" viewBox="0 0 18 14" aria-hidden="true">
            <path d="M1 2 L17 2 L17 12 L1 12 Z M2.5 3.5 L9 8 L15.5 3.5 L15.5 3.2 L2.5 3.2 Z" fill-rule="evenodd"/>
          </svg>
          <span>teodoro@kestrelpicturehouse.example</span>
        </li>
        <li class="contact__item">
          <svg class="contact__icon" viewBox="0 0 18 14" aria-hidden="true">
            <path d="M9 0.5 A6.5 6.5 0 1 0 9 13.5 A6.5 6.5 0 1 0 9 0.5 Z M9 2 A5 5 0 1 1 9 12 A5 5 0 1 1 9 2 Z M3 6.3 L15 6.3 L15 7.7 L3 7.7 Z M8.3 1 L9.7 1 L9.7 13 L8.3 13 Z" fill-rule="evenodd"/>
          </svg>
          <span>www.kestrelpicturehouse.example</span>
        </li>
      </ul>
      <div class="social" aria-label="Social media">
        <span class="social__dot" role="img" aria-label="Social network profile"></span>
        <span class="social__dot" role="img" aria-label="Social network profile"></span>
        <span class="social__handle">/kestrelpicturehouse</span>
      </div>
    </div>
  </section>
</main>
</body>
</html>
```